co working space / serviced office/ business centre

Brevlo - brevlo.in, is a very young brand bieng run by 3 young entrepreneurs. We want to be become out of the league company delivering fabulous and beautiful serviced offices in India and abroad. We hire designers who have made spaces across the world. We want to get visiting card design which gives complete fresh look to the people who carries that card, has to be very impactful and should symbolise happy young and energetic brand. should be completely out of the box thinking of international level, should portray global brand image.

Target Market(s)

Startups, (Small, medium and large corporates)

Industry/Entity Type

Business

Contact Information for Business Card

Name, Email, Address, Mobile number, Landline number, website

Colors

Designer to choose colors to be used in the design.

Requirements
Must have
• Nice new shape
Nice to have
• We want creative cuts, different size and impactful brand clarity
Should not have
• Boring and regular design and shape

```html
<!DOCTYPE html>
<html lang="en">
<head>
<meta charset="utf-8">
<title>Brevlo business card</title>
<link href="https://fonts.googleapis.com/css2?family=Work+Sans:wght@400;600;700&display=swap" rel="stylesheet">
<style>
  :root {
    --red: #ec1c24;
    --ink: #161616;
    --paper: #ffffff;
    --stage: #ece7e1;
    --text: #222222;
  }
  * { margin: 0; padding: 0; box-sizing: border-box; }
  html, body { width: 1200px; height: 930px; overflow: hidden; }
  body {
    background: var(--stage);
    font-family: "Work Sans", sans-serif;
    position: relative;
  }
  .card {
    position: absolute;
    left: 278px;
    width: 644px;
    height: 368px;
    border-radius: 22px;
    overflow: hidden;
    box-shadow: 0 10px 24px rgba(0,0,0,0.18);
  }
  .card--front { top: 76px; background: var(--paper); }
  .card--back { top: 486px; background: var(--ink); }

  .wordmark { position: absolute; text-align: center; color: var(--red); }
  .wordmark__name {
    font-weight: 700;
    letter-spacing: 2px;
    line-height: 1;
    display: block;
  }
  .wordmark__rule { display: block; background: var(--red); }
  .wordmark__tagline {
    display: block;
    font-weight: 600;
    line-height: 1;
  }

  .card--front .wordmark { left: 31px; top: 108px; width: 241px; }
  .card--front .wordmark__name { font-size: 46px; }
  .card--front .wordmark__rule { margin-top: 7px; height: 2px; }
  .card--front .wordmark__tagline { font-size: 12px; margin-top: 12px; letter-spacing: 4px; }

  .card--back .wordmark { left: 173px; top: 182px; width: 298px; }
  .card--back .wordmark__name { font-size: 54px; }
  .card--back .wordmark__rule { margin-top: 10px; height: 3px; }
  .card--back .wordmark__tagline { font-size: 16px; margin-top: 14px; letter-spacing: 5px; }

  .person { position: absolute; right: 31px; top: 194px; text-align: right; }
  .person__name {
    color: var(--red);
    font-size: 32px;
    font-weight: 600;
    line-height: 1;
  }
  .person__role { font-size: 15px; color: var(--text); margin-top: 4px; }
  .divider {
    position: absolute;
    left: 32px;
    top: 236px;
    width: 513px;
    height: 1.5px;
    background: var(--red);
  }

  .contacts {
    position: absolute;
    top: 264px;
    list-style: none;
    font-size: 15px;
    color: var(--text);
    line-height: 20px;
  }
  .contacts li { display: flex; align-items: center; gap: 10px; }
  .contacts svg { width: 12px; height: 12px; flex: none; }
  .contacts--phone { left: 32px; }
  .contacts--web { right: 29px; }
  .contacts--web li { justify-content: flex-end; }

  .address-band {
    position: absolute;
    left: 0; right: 0; top: 330px;
    height: 26px;
    background: var(--ink);
    color: #ffffff;
    font-size: 15px;
    text-align: center;
    line-height: 26px;
  }
  .accent-band {
    position: absolute;
    left: 0; right: 0; top: 356px;
    height: 12px;
    background: var(--red);
  }
</style>
</head>
<body>

<section class="card card--front">
  <div class="wordmark">
    <span class="wordmark__name">BREVLO</span>
    <span class="wordmark__rule"></span>
    <span class="wordmark__tagline">MEET. PLAN. GROW</span>
  </div>

  <div class="person">
    <div class="person__name">ARAN MEHTA</div>
    <div class="person__role">Director</div>
  </div>
  <div class="divider"></div>

  <ul class="contacts contacts--phone">
    <li>
      <svg viewBox="0 0 12 12" aria-hidden="true"><path d="M3 1 L5 3.5 L4 5 Q5 7 7 8 L8.5 7 L11 9 L9.5 11 Q4 10.5 1 3 Z" fill="var(--red)"/></svg>
      <span>520 418 0246</span>
    </li>
    <li>
      <svg viewBox="0 0 12 12" aria-hidden="true"><rect x="2.5" y="0.5" width="7" height="11" rx="1.2" fill="none" stroke="var(--red)" stroke-width="1.4"/><rect x="4" y="2" width="4" height="6.5" fill="var(--red)"/></svg>
      <span>820 517 3094</span>
    </li>
  </ul>

  <ul class="contacts contacts--web">
    <li>
      <span>info@Brevlo.com</span>
      <svg viewBox="0 0 12 12" aria-hidden="true"><rect x="1" y="2.5" width="10" height="7" fill="none" stroke="var(--red)" stroke-width="1.3"/><path d="M1 3 L6 6.5 L11 3" fill="none" stroke="var(--red)" stroke-width="1.3"/></svg>
    </li>
    <li>
      <span>www.Brevlo.com</span>
      <svg viewBox="0 0 12 12" aria-hidden="true"><g fill="none" stroke="var(--red)" stroke-width="1"><circle cx="6" cy="6" r="5"/><ellipse cx="6" cy="6" rx="2.2" ry="5"/><path d="M1 6 H11 M2 3.5 H10 M2 8.5 H10"/></g></svg>
    </li>
  </ul>

  <div class="address-band">1400 North Maple Road Dayton, OH 45402</div>
  <div class="accent-band"></div>
</section>

<section class="card card--back">
  <div class="wordmark">
    <span class="wordmark__name">BREVLO</span>
    <span class="wordmark__rule"></span>
    <span class="wordmark__tagline">MEET. PLAN. GROW</span>
  </div>
</section>

</body>
</html>
```